Book Cover for Lantern Cousins Notes from the Orchard

We have written a book that brings together Notes from the Orchard from a variety of women's voices.
We developed a draft book cover that we like using Canva (attached below). We'd love a book cover that is similar to this image, but looks more professional.
Following are the themes we’d like to depict in the book cover, and in parentheses, how they are represented in the current cover:
1. Divinely feminine (overall cover)
2. Currents of enlightenment (the swirls of light carrying the butterfly)
3. Diversity (a myriad of colors)
4. The solo journey into the unknown (the single butterfly’s flight)
5. Buoyancy and joy (again, the dancing colors and floating butterfly)
6. Boldly feminine (the blue butterfly, set against brush strokes of light)
7. Homage to a dear friend (she loved blue butterflies, the cosmos - this butterfly has hints of the cosmos in her wings, and painting - this background has brush strokes of light).
Book Title, Subtitle, and Editor:
Lantern Cousins
Notes from the Orchard
Edited by Ilse Varno
Thank you very much for considering this project!
People who are interested in Women and Spirituality

```html
<!DOCTYPE html>
<html lang="en">
<head>
<meta charset="utf-8">
<title>Lantern Cousins — Notes from the Orchard</title>
<link rel="stylesheet" href="https://fonts.googleapis.com/css2?family=Marcellus&family=Great+Vibes&display=swap">
<style>
  :root {
    --backdrop: #cbcbcb;
    --cover: #ffffff;
    --cover-shade: #f3f3f3;
    --title-purple: #7b3f98;
    --rule-pink: #dcb6d4;
    --ink: #1a1a1a;
    --wing-purple: #7d3f9a;
    --wing-blue: #1e9ad8;
    --wing-green: #8cc63f;
    --wing-yellow: #e6df2c;
    --wing-orange: #f39a1e;
    --wing-red: #e5472a;
  }
  * { box-sizing: border-box; margin: 0; padding: 0; }
  html, body {
    width: 1200px;
    height: 1200px;
    overflow: hidden;
    background: var(--backdrop);
  }
  .canvas {
    position: relative;
    width: 1200px;
    height: 1200px;
    display: flex;
    align-items: center;
    justify-content: center;
  }
  .book-cover {
    position: relative;
    width: 770px;
    height: 1160px;
    background: linear-gradient(180deg, var(--cover) 0%, var(--cover) 60%, var(--cover-shade) 100%);
    display: flex;
    flex-direction: column;
    align-items: center;
  }
  .title {
    margin-top: 92px;
    font-family: "Marcellus", serif;
    font-weight: 400;
    color: var(--title-purple);
    text-align: center;
    text-transform: uppercase;
    line-height: 0.95;
    font-size: 118px;
    letter-spacing: 1px;
  }
  .title span { display: block; }
  .subtitle-block {
    margin-top: 40px;
    width: 460px;
    display: flex;
    flex-direction: column;
    align-items: center;
  }
  .subtitle-rule {
    width: 100%;
    height: 1px;
    background: linear-gradient(90deg, transparent 0%, var(--rule-pink) 18%, var(--rule-pink) 82%, transparent 100%);
  }
  .subtitle {
    font-family: "Great Vibes", cursive;
    font-size: 54px;
    color: var(--ink);
    padding: 14px 0 16px;
    line-height: 1;
    white-space: nowrap;
  }
  .butterfly-art {
    margin-top: 60px;
    width: 420px;
    height: 400px;
    display: block;
  }
  .editor {
    margin-top: auto;
    margin-bottom: 96px;
    font-family: "Marcellus", serif;
    color: var(--ink);
    text-transform: uppercase;
    font-size: 34px;
    letter-spacing: 2px;
    white-space: nowrap;
  }
  .editor-name {
    font-size: 38px;
    font-weight: 400;
    -webkit-text-stroke: 0.6px var(--ink);
  }
</style>
</head>
<body>
<main class="canvas">
  <article class="book-cover">
    <h1 class="title">
      <span>Lantern</span>
      <span>Cousins</span>
    </h1>
    <div class="subtitle-block">
      <div class="subtitle-rule"></div>
      <p class="subtitle">Notes from the Orchard</p>
      <div class="subtitle-rule"></div>
    </div>
    <svg class="butterfly-art" viewBox="0 0 420 400" role="img" aria-label="Butterfly illustration made of rainbow-coloured paint strokes and scattered dots, purple at the wing tips fading through blue and green to orange and red">
      <defs>
        <linearGradient id="wing-spectrum" x1="0" y1="0" x2="0" y2="1">
          <stop offset="0.05" stop-color="var(--wing-purple)"/>
          <stop offset="0.32" stop-color="var(--wing-blue)"/>
          <stop offset="0.52" stop-color="var(--wing-green)"/>
          <stop offset="0.66" stop-color="var(--wing-yellow)"/>
          <stop offset="0.8" stop-color="var(--wing-orange)"/>
          <stop offset="0.95" stop-color="var(--wing-red)"/>
        </linearGradient>
        <radialGradient id="wing-fade" cx="0.5" cy="0.5" r="0.5">
          <stop offset="0" stop-color="#fff" stop-opacity="1"/>
          <stop offset="0.45" stop-color="#fff" stop-opacity="0.9"/>
          <stop offset="1" stop-color="#fff" stop-opacity="0"/>
        </radialGradient>
        <mask id="soft-edge" maskUnits="userSpaceOnUse" x="0" y="0" width="420" height="400">
          <ellipse cx="210" cy="200" rx="200" ry="190" fill="url(#wing-fade)"/>
        </mask>
      </defs>
      <rect width="420" height="400" fill="url(#wing-spectrum)" opacity="0.85" mask="url(#soft-edge)"/>
    </svg>
    <p class="editor">Edited by <span class="editor-name">Ilse Varno</span></p>
  </article>
</main>
</body>
</html>
```